Bluecrest Learning Corps by graduating students from college in two years

Based on the logo design, create stationary and business cards for
Dr. Venrel T Oskamp, CEO, (703) 482-1736
and Marisa Deltoft, Respresentative, (301) 647-2208
Address: 4719 Pellham Court, Marrowick Station, VA 22187
Incorporate elelments of the logo

Target Market(s)

USA

Font styles to use
Other font styles liked:
• match with the logo type style

```html
<!DOCTYPE html>
<html lang="en">
<head>
<meta charset="utf-8">
<title>Bluecrest Learning Corps Letterhead</title>
<link href="https://fonts.googleapis.com/css2?family=Arimo:wght@400;700&family=Poppins:wght@600&display=swap" rel="stylesheet">
<style>
  :root {
    --navy: #0f2461;
    --gold: #f0c22f;
    --paper: #ffffff;
    --backdrop: #e6e6e6;
    --body-text: #555a60;
    --heading: #3c3f44;
  }
  * { margin: 0; padding: 0; box-sizing: border-box; }
  html, body { width: 1200px; height: 960px; overflow: hidden; }
  body {
    background: var(--backdrop);
    font-family: "Arimo", Arial, sans-serif;
    display: flex; align-items: center; justify-content: center;
  }
  .letterhead {
    position: relative;
    width: 700px; height: 906px;
    background: var(--paper);
    box-shadow: 0 4px 18px rgba(0,0,0,.12);
    overflow: hidden;
  }
  .brand {
    position: absolute; top: 62px; left: 64px;
    display: flex; align-items: center; gap: 12px;
  }
  .brand-dot { width: 44px; height: 44px; border-radius: 50%; background: var(--gold); }
  .brand-name {
    font-weight: 700; font-size: 17px; color: var(--navy); letter-spacing: .3px;
  }
  .letter-body { position: absolute; top: 250px; left: 64px; width: 540px; }
  .salutation {
    font-family: "Poppins", Arial, sans-serif;
    font-weight: 600; font-size: 17px; color: var(--heading);
    margin-bottom: 18px;
  }
  .letter-body p {
    font-size: 11.5px; line-height: 1.38; color: var(--body-text);
    margin-bottom: 16px;
  }
  .closing {
    font-family: "Poppins", Arial, sans-serif;
    font-weight: 600; font-size: 9.5px; color: var(--heading);
    margin-top: 30px;
  }
  .signature {
    display: block; width: 150px; height: 34px; margin-top: 20px;
    background: linear-gradient(90deg, #d9dbe0, #eef0f3);
    border-radius: 4px;
  }
  .footer-art { position: absolute; left: 0; bottom: 0; width: 700px; height: 200px; }
  .cap-motif {
    position: absolute; left: 620px; bottom: 112px; width: 64px; height: 64px;
    background: linear-gradient(135deg, #1c3578, #0a1b4d);
    border-radius: 6px;
  }
  .contact-strip {
    position: absolute; left: 40px; bottom: 22px; height: 86px;
    display: flex; align-items: center; gap: 20px;
    color: var(--navy); font-size: 12.5px; line-height: 1.3;
  }
  .contact-name { font-weight: 700; font-size: 14px; }
  .contact-phone { display: flex; align-items: center; gap: 5px; }
  .contact-phone svg { width: 11px; height: 11px; fill: var(--navy); }
  .divider { width: 1px; height: 40px; background: var(--navy); }
</style>
</head>
<body>
<main class="letterhead">
  <div class="brand">
    <span class="brand-dot"></span>
    <span class="brand-name">Bluecrest Learning Corps</span>
  </div>

  <section class="letter-body">
    <h1 class="salutation">Dear Mr. Halden,</h1>
    <p>Lorem ipsum dolor sit amet, consectetuer adipiscing elit, sed diam nonummy nibh euismod tincidunt ut laoreet dolore magna aliquam erat volutpat. Ut wisi enim ad minim veniam, quis nostrud exerci tation ullamcorper suscipit lobortis nisl ut aliquip ex ea commodo consequat. Duis autem vel eum iriure dolor in hendrerit in vulputate velit esse molestie consequat, vel illum dolore eu feugiat.</p>
    <p>Rorem ipsum dolor sit amet, consectetuer adipiscing elit, sed diam nonummy nibh euismod tincidunt ut laoreet dolore magna aliquam erat volutpat. Ut wisi enim ad minim veniam, quis nostrud exerci tation ullamcorper suscipit lobortis nisl ut aliquip ex ea commodo consequat. Duis autem vel eum iriure dolor in hendrerit in vulputate velit esse molest.</p>
    <p>Dorem ipsum dolor sit amet, consectetuer adipiscing elit, sed diam nonummy nibh euismod tincidunt ut laoreet dolore magna aliquam erat volutpat. Ut wisi enim ad minim veniam, quis nostrud exerci tation ullamcorper suscipit lobortis nisl ut aliquip ex ea commodo consequat. Duis autem vel eum iriure dolor in hendrerit in vulputate velit esse molestie consequat, vel illum.</p>
    <p>Sorem ipsum dolor sit amet, consectetuer adipiscing elit, sed diam nonummy nibh euismod tincidunt ut laoreet dolore magna aliquam erat volutpat. Ut wisi enim ad minim veniam, quis nostrud exerci tation ullamcorper suscipit lobortis nisl ut aliquip ex ea commodo consequat. Duis autem vel eum iriure dolor in.</p>
    <div class="closing">Sincerely,</div>
    <span class="signature" role="img" aria-label="Handwritten signature"></span>
  </section>

  <svg class="footer-art" viewBox="0 0 700 200" aria-hidden="true">
    <polygon points="0,92 600,92 540,178 0,178" fill="var(--gold)"/>
    <polygon points="540,178 600,92 615,12 700,12 700,178" fill="var(--navy)"/>
  </svg>
  <div class="cap-motif" role="img" aria-label="Graduation cap motif"></div>

  <div class="contact-strip">
    <div>
      <div class="contact-name">Dr. Venrel T Oskamp</div>
      <div>CEO</div>
      <div class="contact-phone"><svg viewBox="0 0 24 24"><path d="M6.6 10.8a15.1 15.1 0 0 0 6.6 6.6l2.2-2.2a1 1 0 0 1 1-.25 11.4 11.4 0 0 0 3.6.57 1 1 0 0 1 1 1V20a1 1 0 0 1-1 1A17 17 0 0 1 3 4a1 1 0 0 1 1-1h3.5a1 1 0 0 1 1 1c0 1.25.2 2.45.57 3.6a1 1 0 0 1-.25 1z"/></svg>(703) 482-1736</div>
    </div>
    <span class="divider"></span>
    <div>
      <div class="contact-name">Marisa Deltoft</div>
      <div>Respresentative</div>
      <div class="contact-phone"><svg viewBox="0 0 24 24"><path d="M6.6 10.8a15.1 15.1 0 0 0 6.6 6.6l2.2-2.2a1 1 0 0 1 1-.25 11.4 11.4 0 0 0 3.6.57 1 1 0 0 1 1 1V20a1 1 0 0 1-1 1A17 17 0 0 1 3 4a1 1 0 0 1 1-1h3.5a1 1 0 0 1 1 1c0 1.25.2 2.45.57 3.6a1 1 0 0 1-.25 1z"/></svg>(301) 647-2208</div>
    </div>
    <span class="divider"></span>
    <div>
      <div>4719 Pellham Court</div>
      <div>Marrowick Station</div>
      <div>VA 22187</div>
    </div>
  </div>
</main>
</body>
</html>
```